Calder Vane LED - E- Commerce site

We need a website designed for an LED Billboard company that sells:
1) LED Billboards (Sales & Rental)
2) LED Gas Station lights
3) Truss Systems (Sales & Rental)
4) Sound Systems (Sales & Rental)

Attached are websites that sell similar products as Calder Vane LED. Target market is for business, property managers and event coordinators.
This site will need to be an e-commerce site where customers can purchase the product directly from the site. What I'm looking for is a design layout to start.

Conceptual Web Designs:
http://192.0.2.47:8087/index.html
http://www.pmvdisplay.example/
http://www.auralomaaudio.example/
http://www.quillmarkpanel.example/

Attached is the logo of the company: Please note that the new spelling of the logo is "Calder Vane LED" using domain " CalderVaneLED.com

Industry/Entity Type

Gas Station

Number of Pages Required

5+ page

Requirements
Must have
• 1) E-Commerce - Customers will need to be able to order product from the site.
• 2) Customers will also have the option to rent the product as well.
Nice to have
• I like the image of the attached website, that has a video clip loop
• http://www.quillmarkpanel.example/

```html
<!DOCTYPE html>
<html lang="en">
<head>
<meta charset="utf-8">
<title>Calder Vane LED</title>
<link rel="stylesheet" href="https://fonts.googleapis.com/css2?family=Orbitron:wght@700;900&family=Questrial&display=swap">
<style>
:root{
  --black:#000;
  --ink:#222;
  --muted:#555;
  --light:#efefef;
  --line:#d9d9d9;
  --blue:#1b5fae;
  --red:#e2213a;
  --yellow:#ffd400;
  --purple:#6a2b8f;
  --pink:#e3146f;
  --green:#1ccf95;
  --orange:#f7941d;
  --gold:#f4b21b;
  --navy:#0b2c5c;
  --hero-gold:#f5b800;
}
*{box-sizing:border-box;margin:0;padding:0}
html,body{width:1200px;height:2290px;overflow:hidden}
body{position:relative;background:#fff;font-family:'Questrial',sans-serif;color:var(--ink);font-size:14px}
.display{font-family:'Orbitron',sans-serif;font-weight:900;letter-spacing:1px}
.abs{position:absolute}
a{color:inherit;text-decoration:none}

/* top bar */
.topbar{left:0;top:0;width:1200px;height:46px;background:var(--light);font-size:13px;color:#777}
.topbar .left{left:100px;top:15px;display:flex;gap:32px}
.topbar .right{right:100px;top:15px;display:flex;gap:30px}
.topbar .hot{color:var(--red)}
.ico{display:inline-block;width:11px;height:11px;vertical-align:-1px;margin-right:7px}

/* header */
.header{left:0;top:46px;width:1200px;height:116px;background:#0b0b0b}
.brand{left:100px;top:24px;display:flex;align-items:center;gap:12px}
.brand .dot{width:64px;height:64px;border-radius:50%;background:var(--gold)}
.brand .name{font-family:'Questrial',sans-serif;font-size:24px;color:#fff}
.search{left:606px;top:46px;width:315px;height:34px;display:flex}
.search .field{flex:1;background:#fff;color:#aaa;font-size:12px;padding:10px 14px}
.search .go{width:40px;background:#e2262c;display:flex;align-items:center;justify-content:center}
.cart{left:968px;top:50px;display:flex;align-items:center;gap:13px;color:#fff;font-size:13px}
.cart .bag{width:28px;height:28px;border-radius:50%;background:var(--gold)}

/* nav */
.nav{left:100px;top:162px;width:1001px;height:82px;display:flex;background:#fff}
.nav a{flex:1;display:flex;align-items:center;justify-content:center;font-size:13px;color:var(--ink);border-bottom:6px solid;border-right:1px solid #eee}
.nav a.active{background:var(--blue);color:#fff}
.nav .c1{border-color:var(--blue)}.nav .c2{border-color:var(--red)}.nav .c3{border-color:var(--yellow)}
.nav .c4{border-color:var(--purple)}.nav .c5{border-color:var(--pink)}.nav .c6{border-color:var(--blue)}

/* hero */
.hero{left:0;top:244px;width:1200px;height:408px;background:radial-gradient(ellipse at 30% 60%,#1a2b52 0%,#0a1024 50%,#04060e 100%)}
.hero h1{left:145px;top:102px;font-size:28px;color:var(--hero-gold)}
.hero p{left:145px;top:158px;width:520px;font-size:20px;line-height:37px;color:#fff}
.hero .cta{left:145px;top:290px;width:272px;height:58px;border:2px solid var(--pink);color:#fff;font-size:23px;display:flex;align-items:center;justify-content:center}
.hero .product{left:672px;top:105px;width:322px;height:250px;border-radius:10px;background:linear-gradient(145deg,#c9c9c9,#6c6c6c 60%,#3a3a3a)}
.arrow{width:40px;height:40px;border-radius:50%;background:#2d2d2d;display:flex;align-items:center;justify-content:center;top:186px}

/* category banners */
.banner{width:491px;height:146px;color:#fff;padding:55px 30px}
.banner h2{font-size:29px}
.banner small{display:block;margin-top:8px;font-size:12px}
.banner .art{position:absolute;right:20px;top:14px;width:170px;height:118px;border-radius:8px}
.b1{left:100px;top:669px;background:linear-gradient(90deg,#000,#1a1a1a)}
.b1 .art{background:linear-gradient(180deg,#f1f1f1,#777)}
.b2{left:609px;top:669px;background:var(--green)}
.b2 .art{background:radial-gradient(circle,#fff,#c9efe0 60%,transparent 70%)}
.b3{left:100px;top:831px;background:linear-gradient(135deg,#0e3466,#07234a)}
.b3 .art{background:radial-gradient(circle,#fff,#9cc5f1 55%,transparent 70%)}
.b4{left:609px;top:831px;background:var(--orange)}
.b4 .art{background:linear-gradient(90deg,#fff,#e8e8e8)}

/* categories */
.side{left:100px;top:1000px;width:243px}
.sectionhead{background:var(--black);color:#fff;height:67px;display:flex;align-items:center;padding-left:12px;font-size:23px}
.side li{list-style:none;background:var(--light);height:54px;margin-top:3px;display:flex;align-items:center;padding-left:12px;font-size:14px;color:#555}
.side li::before{content:'›';color:var(--red);margin-right:12px;font-size:16px}
.featured{left:357px;top:1000px;width:744px}
.sectionhead .more{font-family:'Questrial',sans-serif;font-weight:400;font-size:12px;color:var(--gold);margin-left:14px;letter-spacing:0}
.sectionhead .pager{margin-left:auto;margin-right:14px;display:flex;gap:12px}

/* product cards */
.card{width:220px;height:321px;border:1px solid var(--line);text-align:center;padding:4px}
.card.hl{border-color:var(--gold)}
.card .thumb{height:178px;border:1px solid var(--line);background:linear-gradient(180deg,#fafafa,#e2e2e2)}
.card h3{font-size:14px;margin-top:18px;font-weight:700;letter-spacing:.5px}
.card p{font-size:12px;color:#555;line-height:23px;margin-top:6px}
.card .btns{position:absolute;left:4px;right:4px;bottom:4px;display:flex;gap:8px}
.card .btns span{flex:1;height:40px;border:1px solid var(--line);font-size:12px;display:flex;align-items:center;justify-content:center}
.card.hl .btns span{border-color:var(--gold)}
.card .price{position:absolute;left:60px;top:75px;background:var(--gold);color:#fff;font-size:17px;padding:8px 14px}
.rowhead{left:100px;top:1418px;width:1001px}

/* promos */
.promo{top:1843px;width:531px;height:175px;color:#fff;display:flex;align-items:center}
.promo .ring{width:140px;height:140px;border:3px solid #fff;border-radius:50%;margin-left:43px;display:flex;align-items:center;justify-content:center}
.promo h2{font-size:28px;margin-left:38px}
.promo p{font-size:18px;margin-left:38px;margin-top:8px;letter-spacing:1px}
.p1{left:100px;background:var(--pink)}
.p2{left:614px;width:486px;background:var(--gold)}

/* footer */
.footer{left:0;top:2037px;width:1200px;height:171px;background:var(--light)}
.fcol{top:26px}
.fcol h4{font-size:16px;color:#333;border-bottom:1px solid #555;padding-bottom:4px;width:176px}
.fcol ul{list-style:none;margin-top:12px}
.fcol li{font-size:10px;color:#666;line-height:19px;text-transform:uppercase}
.fcol li::before{content:'▪';margin-right:8px;font-size:8px}
.fcol .plain li::before{content:none}
.fcol .plain li{text-transform:none}
.paybar{left:0;top:2208px;width:1200px;height:43px;background:#e2e2e2}
.pill{height:26px;background:#4a86c8;color:#fff;font-size:13px;display:flex;align-items:center;justify-content:center;top:8px}
.card-chip{top:7px;width:44px;height:29px;border-radius:3px}
.social{top:7px;width:30px;height:30px;border-radius:4px}
.copy{left:0;top:2251px;width:1200px;height:39px;background:#1a1a1a;color:#ddd;font-size:12px;display:flex;align-items:center;justify-content:center}
.copy .code{position:absolute;right:40px;color:#aaa}
</style>
</head>
<body>

<div class="abs topbar">
  <div class="abs left">
    <span><svg class="ico" viewBox="0 0 12 12"><path d="M2 1l3 2-1 2 3 3 2-1 2 3-2 2C5 11 1 7 0 3z" fill="#e2262c"/></svg>214-555-0148</span>
    <span><svg class="ico" viewBox="0 0 12 12"><rect x="0" y="2" width="12" height="8" fill="#e2262c"/><path d="M0 2l6 4 6-4" stroke="#fff" fill="none"/></svg>Sales@NorthgateRewards.example</span>
  </div>
  <div class="abs right">
    <span><svg class="ico" viewBox="0 0 12 12"><path d="M1 11l2-5 6-6 3 3-6 6z" fill="#e2262c"/></svg>Registration</span>
    <span><svg class="ico" viewBox="0 0 12 12"><circle cx="6" cy="3.5" r="3" fill="#e2262c"/><path d="M0 12c0-4 12-4 12 0z" fill="#e2262c"/></svg>Login</span>
    <span class="hot">My Account</span>
    <span>Check out</span>
    <span>Delivery</span>
  </div>
</div>

<header class="abs header">
  <div class="abs brand"><span class="dot"></span><span class="name">Calder Vane LED</span></div>
  <div class="abs search">
    <div class="field">Search your Product...</div>
    <div class="go"><svg width="14" height="14" viewBox="0 0 14 14"><circle cx="6" cy="6" r="4.5" stroke="#fff" stroke-width="2" fill="none"/><path d="M9.5 9.5L13 13" stroke="#fff" stroke-width="2"/></svg></div>
  </div>
  <div class="abs cart"><span class="bag"></span>$ 00.00 (0 Items)</div>
</header>

<nav class="abs nav">
  <a class="c1 active">Home ⌄</a>
  <a class="c2">About us</a>
  <a class="c3">Our services ⌄</a>
  <a class="c4">Blog</a>
  <a class="c5">Our Products ⌄</a>
  <a class="c6">Contact us</a>
</nav>

<section class="abs hero">
  <h1 class="abs display">CALDER VANE LED</h1>
  <p class="abs">We are focused in delivering best in class customer service with a team of highly experienced lighting professionals</p>
  <a class="abs cta">PURCHASE NOW</a>
  <div class="abs product" role="img" aria-label="LED flood light fixture"></div>
  <div class="abs arrow" style="left:32px"><svg width="14" height="14" viewBox="0 0 14 14"><path d="M10 1L3 7l7 6" stroke="#fff" stroke-width="3" fill="none"/></svg></div>
  <div class="abs arrow" style="left:1128px"><svg width="14" height="14" viewBox="0 0 14 14"><path d="M4 1l7 6-7 6" stroke="#fff" stroke-width="3" fill="none"/></svg></div>
</section>

<a class="abs banner b1"><h2 class="display">BILLBOARDS</h2><small>Click Here To View The Flip Book</small><span class="art" role="img" aria-label="Lit LED billboard"></span></a>
<a class="abs banner b2"><h2 class="display">CRYSTAL</h2><small>Click Here To View The Flip Book</small><span class="art" role="img" aria-label="Glowing light bulb"></span></a>
<a class="abs banner b3"><h2 class="display">CORPERA</h2><small>Click Here To View The Flip Book</small><span class="art" role="img" aria-label="Spiral energy saving bulb"></span></a>
<a class="abs banner b4"><h2 class="display">STREET</h2><small>Click Here To View The Flip Book</small><span class="art" role="img" aria-label="Compact fluorescent tube lamp"></span></a>

<aside class="abs side">
  <div class="sectionhead display">CATEGORIES</div>
  <ul>
    <li>LED Billboards</li><li>Trusses</li><li>Gas Station lights</li>
    <li>LED Billboards</li><li>Trusses</li><li>Gas Station lights.</li>
  </ul>
</aside>

<section class="abs featured">
  <div class="sectionhead display">FEATURED PRODUCTS<span class="more">VIEW ALL →</span>
    <span class="pager"><svg width="14" height="22" viewBox="0 0 14 22"><path d="M12 2L3 11l9 9" stroke="#fff" stroke-width="3" fill="none"/></svg><svg width="14" height="22" viewBox="0 0 14 22"><path d="M2 2l9 9-9 9" stroke="#fff" stroke-width="3" fill="none"/></svg></span>
  </div>
</section>

<div class="abs card hl" style="left:357px;top:1081px">
  <div class="thumb" role="img" aria-label="LED flood light"></div>
  <span class="price">$350</span>
  <h3>LED FLOOD LIGHTS</h3><p>Lights for Factories, gymnasiums,<br>yards, advertising boards, buildings.</p>
  <div class="btns"><span>ADD TO CART</span><span>DETAILS</span></div>
</div>
<div class="abs card" style="left:615px;top:1081px">
  <div class="thumb" role="img" aria-label="Illuminated display panel"></div>
  <h3>LED FLOOD LIGHTS</h3><p>Lights for Factories, gymnasiums,<br>yards, advertising boards, buildings.</p>
  <div class="btns"><span>ADD TO CART</span><span>DETAILS</span></div>
</div>
<div class="abs card" style="left:875px;top:1081px">
  <div class="thumb" role="img" aria-label="Square truss frame"></div>
  <h3>LED FLOOD LIGHTS</h3><p>Lights for Factories, gymnasiums,<br>yards, advertising boards, buildings.</p>
  <div class="btns"><span>ADD TO CART</span><span>DETAILS</span></div>
</div>

<div class="abs rowhead">
  <div class="sectionhead display">LED BILLBOARDS AND TRUSSES<span class="more">VIEW ALL →</span>
    <span class="pager"><svg width="14" height="22" viewBox="0 0 14 22"><path d="M12 2L3 11l9 9" stroke="#fff" stroke-width="3" fill="none"/></svg><svg width="14" height="22" viewBox="0 0 14 22"><path d="M2 2l9 9-9 9" stroke="#fff" stroke-width="3" fill="none"/></svg></span>
  </div>
</div>

<div class="abs card" style="left:100px;top:1504px">
  <div class="thumb" role="img" aria-label="Blank billboard on a pole"></div>
  <h3>BILL BOARDS</h3><p>Lights for Factories, gymnasiums,<br>yards, advertising boards, buildings.</p>
  <div class="btns"><span>ADD TO CART</span><span>DETAILS</span></div>
</div>
<div class="abs card" style="left:359px;top:1504px">
  <div class="thumb" role="img" aria-label="Stage with truss frame"></div>
  <h3>LED FLOOD LIGHTS</h3><p>Lights for Factories, gymnasiums,<br>yards, advertising boards, buildings.</p>
  <div class="btns"><span>ADD TO CART</span><span>DETAILS</span></div>
</div>
<div class="abs card" style="left:617px;top:1504px">
  <div class="thumb" role="img" aria-label="Truss bar with stage lights"></div>
  <h3>BILL BOARDS</h3><p>Lights for Factories, gymnasiums,<br>yards, advertising boards, buildings.</p>
  <div class="btns"><span>ADD TO CART</span><span>DETAILS</span></div>
</div>
<div class="abs card" style="left:875px;top:1504px">
  <div class="thumb" role="img" aria-label="LED flood light"></div>
  <h3>LED FLOOD LIGHTS</h3><p>Lights for Factories, gymnasiums,<br>yards, advertising boards, buildings.</p>
  <div class="btns"><span>ADD TO CART</span><span>DETAILS</span></div>
</div>

<div class="abs promo p1">
  <div class="ring"><svg width="50" height="70" viewBox="0 0 50 70"><rect x="14" y="2" width="22" height="40" rx="11" fill="#fff"/><path d="M6 30c0 24 38 24 38 0" stroke="#fff" stroke-width="4" fill="none"/><path d="M25 52v12M14 66h22" stroke="#fff" stroke-width="4"/></svg></div>
  <div><h2 class="display">ONLINE ORDER</h2><p>HOURS:&nbsp; 06 AM TO 11 PM</p></div>
</div>
<div class="abs promo p2">
  <div class="ring"><svg width="66" height="50" viewBox="0 0 66 50"><rect x="2" y="4" width="38" height="32" fill="#fff"/><path d="M42 14h12l10 12v10H42z" fill="#fff"/><circle cx="14" cy="40" r="7" fill="#fff" stroke="#f4b21b" stroke-width="3"/><circle cx="52" cy="40" r="7" fill="#fff" stroke="#f4b21b" stroke-width="3"/></svg></div>
  <div><h2 class="display">FREE SHIPPING</h2><p>ON ORDERS OVER $799</p></div>
</div>

<footer class="abs footer">
  <div class="abs fcol" style="left:100px"><h4 class="display">INFORMATION</h4><ul><li>Home</li><li>Lights</li><li>Bilboards</li><li>LED Flood</li><li>Services</li></ul></div>
  <div class="abs fcol" style="left:361px"><h4 class="display">WHY BUY</h4><ul><li>About us</li><li>Contact us</li><li>Blog</li><li>Flag cases</li><li>Display Lighting</li></ul></div>
  <div class="abs fcol" style="left:646px"><h4 class="display">MY ACCOUNT</h4><ul><li>Display frames</li><li>Shadow boxes</li><li>Decration</li><li>Annual order</li><li>Form</li></ul></div>
  <div class="abs fcol" style="left:919px"><h4 class="display">CONTACT</h4><ul class="plain"><li>ph: 123 - 456 - 7890</li><li>fax: 408-555-0193</li><li>Sales@caldervaneled.com</li></ul></div>
</footer>

<div class="abs paybar">
  <div class="abs pill" style="left:100px;width:96px">WE ACCEPT</div>
  <span class="abs card-chip" style="left:208px;background:#1a4f9c"></span>
  <span class="abs card-chip" style="left:262px;background:#1e1e1e"></span>
  <span class="abs card-chip" style="left:316px;background:#2e77bb"></span>
  <span class="abs card-chip" style="left:370px;background:#1b4e8f"></span>
  <div class="abs pill" style="left:796px;width:96px">FLLOW US</div>
  <span class="abs social" style="left:908px;background:#3b5998"></span>
  <span class="abs social" style="left:946px;background:#2fa9e0"></span>
  <span class="abs social" style="left:985px;background:#d73d32"></span>
  <span class="abs social" style="left:1025px;background:#1a8bd6"></span>
  <span class="abs social" style="left:1064px;background:#ea4c89"></span>
</div>

<div class="abs copy">© 2016 caldervaneled.com.All Rights Reserved<span class="code">C9</span></div>

</body>
</html>
```